BildeVOLD buisnesscard

Hey :) I need a modern buisnesscard for my company BildeVOLD
It most have:
Dagligleder og Fotograf: Henrik Audun Strandvik

Mob: +4791264085
Epost: post@bildevold.example
Adresse: Kvernbakken9, 6040 Havsøy

Facbook and instagram logo with text BildeVOLD

BildeVOLD logo

It Company

```html
<!DOCTYPE html>
<html lang="no">
<head>
<meta charset="utf-8">
<title>BildeVOLD – visittkort</title>
<link href="https://fonts.googleapis.com/css2?family=Montserrat:wght@400;500;700;800&display=swap" rel="stylesheet">
<style>
  :root {
    --brand-blue: #2279aa;
    --brand-pink: #c83a86;
    --brand-pink-light: #d5519a;
    --paper: #efefef;
    --backdrop: #d6d6d6;
    --white: #ffffff;
  }
  * { margin: 0; padding: 0; box-sizing: border-box; }
  html, body {
    width: 1200px; height: 799px; overflow: hidden;
    background: var(--backdrop);
    font-family: "Montserrat", sans-serif;
  }
  .canvas { position: relative; width: 1200px; height: 799px; }
  .card {
    position: absolute; top: 140px;
    width: 300px; height: 520px;
    overflow: hidden;
    box-shadow: 0 10px 28px rgba(0,0,0,.25);
  }
  .card--front { left: 250px; background: var(--paper); }
  .card--back {
    left: 650px;
    background: linear-gradient(160deg, var(--brand-pink-light) 0%, var(--brand-pink) 60%, #bf3380 100%);
  }
  .card__shapes { position: absolute; inset: 0; }

  .identity {
    position: absolute; top: 34px; right: 22px;
    text-align: right; color: var(--white);
  }
  .identity__name { font-weight: 800; font-size: 15px; letter-spacing: .3px; text-transform: uppercase; }
  .identity__title { font-weight: 700; font-size: 13px; margin-top: 3px; }

  .contact {
    position: absolute; top: 112px; right: 22px;
    list-style: none; text-align: right; color: var(--white);
    font-size: 12.5px; font-weight: 400; line-height: 1.45;
  }
  .contact__row { display: flex; justify-content: flex-end; align-items: center; gap: 7px; }
  .contact__icon { width: 12px; height: 12px; flex: none; }
  .contact__spacer { width: 12px; flex: none; }
  .contact__web strong { font-weight: 700; }

  .wordmark {
    position: absolute; display: flex; align-items: center; gap: 10px;
    font-weight: 800; letter-spacing: .5px;
  }
  .wordmark__mark { flex: none; }
  .card--front .wordmark { right: 24px; bottom: 58px; font-size: 36px; color: var(--brand-blue); }
  .card--front .wordmark__mark { width: 22px; height: 22px; background: var(--brand-pink); }
  .card--back .wordmark {
    left: 0; right: 0; top: 196px; justify-content: center;
    font-size: 38px; color: var(--white);
  }
  .card--back .wordmark__mark { width: 22px; height: 22px; border-radius: 50%; background: var(--white); }

  .social {
    position: absolute; left: 30px; right: 30px; top: 268px;
    display: flex; align-items: center; gap: 8px;
  }
  .social__rule { flex: 1; height: 1px; background: rgba(255,255,255,.7); }
  .social__dot { width: 20px; height: 20px; border-radius: 50%; background: var(--white); }
</style>
</head>
<body>
<main class="canvas">

  <section class="card card--front" aria-label="Forside visittkort">
    <svg class="card__shapes" viewBox="0 0 300 520" width="300" height="520" aria-hidden="true">
      <polygon points="0,0 300,0 300,392 0,288" fill="var(--brand-blue)"/>
      <polygon points="0,288 300,392 300,401 0,297" fill="var(--brand-pink)"/>
    </svg>

    <header class="identity">
      <p class="identity__name">Henrik Audun Strandvik</p>
      <p class="identity__title">Dagligleder og Fotograf</p>
    </header>

    <ul class="contact">
      <li class="contact__row"><span>Kvernbakken9</span><span class="contact__spacer"></span></li>
      <li class="contact__row"><span>6040 Havsøy</span><span class="contact__spacer"></span></li>
      <li class="contact__row"><span>+4791264085</span>
        <svg class="contact__icon" viewBox="0 0 12 12" aria-hidden="true"><rect x="3" y="0.5" width="6" height="11" rx="1.2" fill="none" stroke="#fff" stroke-width="1.2"/><line x1="5" y1="9.6" x2="7" y2="9.6" stroke="#fff" stroke-width="1"/></svg>
      </li>
      <li class="contact__row"><span>post@bildevold.example</span>
        <svg class="contact__icon" viewBox="0 0 12 12" aria-hidden="true"><rect x="0.5" y="2.5" width="11" height="7.5" fill="#fff"/><polyline points="0.5,2.5 6,7 11.5,2.5" fill="none" stroke="var(--brand-blue)" stroke-width="1"/></svg>
      </li>
      <li class="contact__row contact__web"><span>www.<strong>bildevold</strong>.example</span><span class="contact__spacer"></span></li>
    </ul>

    <div class="wordmark"><span class="wordmark__mark"></span>BildeVOLD</div>
  </section>

  <section class="card card--back" aria-label="Bakside visittkort">
    <div class="wordmark"><span class="wordmark__mark"></span>BildeVOLD</div>
    <div class="social" aria-label="Sosiale medier">
      <span class="social__rule"></span>
      <span class="social__dot"></span>
      <span class="social__dot"></span>
      <span class="social__rule"></span>
    </div>
  </section>

</main>
</body>
</html>
```